Business Card for a Jewellery Brand

Business card for an upscale jewellery brand. Attached is the brand logo and icon and color board. I am looking for two card versions: one for the founder and one is generic. The card should be elegant and convey upscale and premium feel. I am open to both square and rectangle card shapes.

Industry/Entity Type

Jewelry

Contact Information for Business Card

Two cards: (1) Sunela Parvaniya (Founder) (2) General
(1) Sunela Parvaniya card should have Name: Sunela Parvaniya, Title: Founder Email id: sunela@quiremo.com.au. Phone no: +61452913307
(2) Generic card should have Email id: info@quiremo.com.au. Phone no: +61436207518

Requirements
Must have
• Workmark
• ICON
• Phone no
• Email ID
• ABN: 58219740312 (Note: ABN is Business number in Australia)
• Website: www.quiremo.com.au
• Instagram: quiremo_jewellery
• Facebook: @quiremojewellery
Nice to have
• Tagline

```html
<!DOCTYPE html>
<html lang="en">
<head>
<meta charset="utf-8">
<title>Quiremo Jewellery – Business Card</title>
<link rel="stylesheet" href="https://fonts.googleapis.com/css2?family=Quicksand:wght@600;700&family=Source+Sans+3:wght@400;600&display=swap">
<style>
  :root {
    --backdrop: #a6a6a6;
    --card-white: #ffffff;
    --blush: #e59895;
    --blush-text: #e8908c;
    --ink: #1e1e1e;
    --on-blush: #ffffff;
  }
  html, body {
    margin: 0;
    padding: 0;
    width: 1200px;
    height: 900px;
    overflow: hidden;
    background: var(--backdrop);
  }
  .canvas {
    position: relative;
    width: 1200px;
    height: 900px;
  }
  .card {
    position: absolute;
    top: 238px;
    width: 400px;
    height: 400px;
    box-sizing: border-box;
    text-align: center;
  }
  .card--front {
    left: 192px;
    background: var(--card-white);
    font-family: "Source Sans 3", sans-serif;
    color: var(--ink);
  }
  .card--back {
    left: 636px;
    background: var(--blush);
    color: var(--on-blush);
  }
  .person-name {
    position: absolute;
    top: 80px;
    left: 0;
    right: 0;
    margin: 0;
    font-family: "Quicksand", sans-serif;
    font-weight: 700;
    font-size: 23px;
    color: var(--blush-text);
  }
  .person-title {
    position: absolute;
    top: 111px;
    left: 0;
    right: 0;
    margin: 0;
    font-size: 18px;
  }
  .abn {
    position: absolute;
    top: 162px;
    left: 0;
    right: 0;
    margin: 0;
    font-size: 17px;
  }
  .abn-label {
    color: var(--blush-text);
    font-weight: 600;
  }
  .contact-icons {
    position: absolute;
    top: 221px;
    left: 165px;
  }
  .contact-list {
    position: absolute;
    top: 248px;
    left: 0;
    right: 0;
    margin: 0;
    padding: 0;
    list-style: none;
    font-size: 20px;
    line-height: 26px;
  }
  .wordmark {
    position: absolute;
    top: 208px;
    left: 0;
    right: 0;
    margin: 0;
    font-family: "Quicksand", sans-serif;
    font-weight: 600;
    font-size: 44px;
    letter-spacing: 0.24em;
    padding-left: 0.24em;
  }
  .social-row {
    position: absolute;
    top: 298px;
    left: 40px;
  }
  .social-handle {
    position: absolute;
    top: 334px;
    left: 0;
    right: 0;
    margin: 0;
    font-family: "Source Sans 3", sans-serif;
    font-size: 17px;
  }
</style>
</head>
<body>
<main class="canvas">
  <section class="card card--front" aria-label="Founder card, contact side">
    <h1 class="person-name">Sunela Parvaniya</h1>
    <p class="person-title">Founder</p>
    <p class="abn"><span class="abn-label">ABN:</span> 58219740312</p>

    <svg class="contact-icons" width="70" height="22" viewBox="0 0 70 22" aria-hidden="true">
      <g fill="#e59895">
        <circle cx="11" cy="11" r="10"/>
        <circle cx="34" cy="11" r="10"/>
        <circle cx="58" cy="11" r="10"/>
      </g>
      <!-- phone -->
      <path d="M7.5 6.5c.6-.6 1.3-.5 1.7.1l1 1.5c.3.5.2 1-.2 1.4l-.6.5c.5 1.1 1.3 1.9 2.4 2.4l.5-.6c.4-.4.9-.5 1.4-.2l1.5 1c.6.4.7 1.1.1 1.7l-.6.6c-.9.9-3 .3-4.9-1.6S6 8 6.9 7.1z" fill="#fff"/>
      <!-- envelope -->
      <rect x="29" y="7.5" width="10" height="7" rx="1" fill="#fff"/>
      <path d="M29.5 8l4.5 3.5L38.5 8" fill="none" stroke="#e59895" stroke-width="1"/>
      <!-- globe -->
      <circle cx="58" cy="11" r="5" fill="none" stroke="#fff" stroke-width="1.2"/>
      <ellipse cx="58" cy="11" rx="2" ry="5" fill="none" stroke="#fff" stroke-width="1"/>
      <line x1="53" y1="11" x2="63" y2="11" stroke="#fff" stroke-width="1"/>
    </svg>

    <ul class="contact-list">
      <li>+61452913307</li>
      <li>sunela@quiremo.com.au</li>
      <li>www.quiremo.com.au</li>
    </ul>
  </section>

  <section class="card card--back" aria-label="Brand side">
    <p class="wordmark">QUIREMO</p>

    <svg class="social-row" width="320" height="26" viewBox="0 0 320 26" aria-hidden="true">
      <g stroke="#fff" stroke-width="1.2">
        <line x1="0" y1="13" x2="114" y2="13"/>
        <line x1="236" y1="13" x2="320" y2="13"/>
      </g>
      <g fill="#fff">
        <circle cx="138" cy="13" r="11.5"/>
        <circle cx="174" cy="13" r="11.5"/>
      </g>
    </svg>

    <p class="social-handle">@quiremojewellery</p>
  </section>
</main>
</body>
</html>
```